Professional Photography Business cards

I need business cards that include my logo which I have uploaded. I run a photography business. I am open to ideas but I would like one side to have my logo and the other side to have my contact info. I don't have a website made but I do own a website domain. I have uploaded 2 different logo color schemes. My business colors are Blue, black , and white.

Business Name
Business Phone Number
Business Email
Business Website address
Instagram

Industry/Entity Type

Professional Photography

Contact Information for Business Card

Phone Number: 916-384-7702 email: info@tlane-studio.example Instagram: @t.lanestudio website doman- www.tlane-studio.example

Requirements
Must have
• I like the idea of a business card with a full black background front and back of card. My colors must include royal blue, black, and white

```html
<!DOCTYPE html>
<html lang="en">
<head>
<meta charset="utf-8">
<title>T. Lane Studio – Business Cards</title>
<link rel="stylesheet" href="https://fonts.googleapis.com/css2?family=Heebo:wght@300;400&display=swap">
<style>
  :root {
    --backdrop: #b8b8b8;
    --card-black: #000000;
    --royal-blue: #000e9c;
    --royal-blue-deep: #000a78;
    --white: #ffffff;
    --shadow: rgba(0,0,0,0.55);
  }
  * { margin: 0; padding: 0; box-sizing: border-box; }
  html, body {
    width: 1200px; height: 801px; overflow: hidden;
    background: var(--backdrop);
    font-family: "Heebo", Arial, sans-serif;
  }
  .sheet { position: relative; width: 1200px; height: 801px; }
  .card {
    position: absolute; top: 274px;
    width: 443px; height: 263px;
    background: var(--card-black);
    box-shadow: 2px 2px 1px var(--shadow);
    overflow: hidden;
  }
  .card--contact { left: 153px; }
  .card--brand { left: 625px; }

  .contact-art { position: absolute; left: 0; top: 0; width: 443px; height: 263px; }

  .contact-list {
    position: absolute; left: 0; top: 0;
    color: var(--white); font-weight: 400; font-size: 13px;
    list-style: none;
  }
  .contact-item {
    position: absolute; left: 24px; white-space: nowrap;
    display: flex; align-items: center; gap: 6px;
    line-height: 1;
  }
  .contact-item svg { width: 12px; height: 12px; flex: none; }
  .contact-item--social { top: 150px; }
  .contact-item--social svg { width: 13px; height: 13px; }
  .contact-item--phone { top: 193px; }
  .contact-item--email { top: 209px; }
  .contact-item--web { top: 225px; }

  .brand {
    position: absolute; left: 0; top: 0; width: 443px; height: 263px;
    display: flex; align-items: center; justify-content: center; gap: 12px;
    padding-top: 10px;
  }
  .brand-mark {
    width: 40px; height: 40px; border-radius: 50%;
    border: 3px solid var(--white);
  }
  .brand-name {
    color: var(--white); font-weight: 300; font-size: 26px;
    letter-spacing: 2px; white-space: nowrap;
  }
</style>
</head>
<body>
<main class="sheet">
  <section class="card card--contact" aria-label="Contact side">
    <svg class="contact-art" viewBox="0 0 443 263" role="img" aria-label="Large royal blue panel where the studio's camera emblem appears as decoration">
      <defs>
        <radialGradient id="panel-glow" cx="298" cy="154" r="80" gradientUnits="userSpaceOnUse">
          <stop offset="0" stop-color="var(--royal-blue-deep)"/>
          <stop offset="1" stop-color="var(--royal-blue)"/>
        </radialGradient>
      </defs>
      <path d="M0 59 H405 Q427 59 427 84 V210 Q427 263 374 263 H0 Z" fill="url(#panel-glow)"/>
    </svg>
    <ul class="contact-list">
      <li class="contact-item contact-item--social">
        <svg viewBox="0 0 12 12"><circle cx="6" cy="6" r="5" fill="none" stroke="#fff" stroke-width="1.4"/></svg>
        <span>@t.lanestudio</span>
      </li>
      <li class="contact-item contact-item--phone">
        <svg viewBox="0 0 12 12"><path d="M2.5 1.2 4.4 1 5.3 3.6 4.1 4.6C4.7 6 6 7.3 7.4 7.9L8.4 6.7 11 7.6 10.8 9.5C10.7 10.3 10 11 9 10.9 5 10.5 1.5 7 1.1 3 1 2 1.7 1.3 2.5 1.2Z" fill="#fff"/></svg>
        <span>916-384-7702</span>
      </li>
      <li class="contact-item contact-item--email">
        <svg viewBox="0 0 12 12"><rect x="0.5" y="2.5" width="11" height="7.5" fill="#fff"/><path d="M0.5 2.8 6 7 11.5 2.8" fill="none" stroke="#000e9c" stroke-width="1"/></svg>
        <span>info@tlane-studio.example</span>
      </li>
      <li class="contact-item contact-item--web">
        <svg viewBox="0 0 12 12" fill="none" stroke="#fff" stroke-width="1"><circle cx="6" cy="6" r="5"/><ellipse cx="6" cy="6" rx="2.2" ry="5"/><path d="M1 6h10M1.8 3.5h8.4M1.8 8.5h8.4"/></svg>
        <span>www.tlane-studio.example</span>
      </li>
    </ul>
  </section>

  <section class="card card--brand" aria-label="Brand side">
    <div class="brand">
      <span class="brand-name">T. Lane Studio</span>
      <span class="brand-mark" aria-hidden="true"></span>
    </div>
  </section>
</main>
</body>
</html>
```